Concierge Dental / Medical Supply Ordering Business - Sleek, Efficient, Professional, Elite

www.brantonkeelmedical.com - example website.

We are a concierge supply ordering business for medical and dental that provide DSO price savings on supplies while maintaining business autonomy and independence.

We want a very simple website that looks very professional says what we do and gives a very simple method to contact us & sign up as above.

Target Market(s)

Independent Dental and Medical Practices

Industry/Entity Type

Dental and Medical - healthcare

Coding

Coded - Design and coding required

Number of Pages Required

3 page

Font styles to use
Sans Serif

Colors
0054AA
0677BA
7BADD7
CADEEF
E8F1F8

Requirements
Must have
• Simple contact page, sleek efficient design, uncomplicated.
Nice to have
• Sign up page vs just a contact page.
Should not have
• Lots of pages, hard to navigate,

```html
<!DOCTYPE html>
<html lang="en">
<head>
<meta charset="utf-8">
<title>Assure Dental Supply</title>
<link href="https://fonts.googleapis.com/css2?family=Poppins:ital,wght@0,400;0,500;0,600;1,700;1,800&family=Arimo:wght@400;500&display=swap" rel="stylesheet">
<style>
:root{
  --accent:#0aa2e8;
  --button:#2f72a8;
  --navy:#063a6c;
  --navy-dark:#04305c;
  --ink:#1a1a1a;
  --text:#2b2b2b;
  --charcoal:#1f1f20;
  --white:#ffffff;
  --line:#6f8fb3;
}
*{margin:0;padding:0;box-sizing:border-box}
html,body{width:1200px;height:3402px;overflow:hidden}
body{position:relative;font-family:"Arimo",Arial,sans-serif;color:var(--text);background:var(--white)}
.abs{position:absolute}
.display{font-family:"Poppins",sans-serif;font-style:italic;font-weight:800;letter-spacing:.3px}
.display .hl{color:var(--accent)}
.btn{position:absolute;display:flex;align-items:center;justify-content:center;font-family:"Poppins",sans-serif;font-style:italic;font-weight:700;font-size:16px;border-radius:2px}
.btn-blue{background:var(--button);color:var(--white)}
.btn-white{background:var(--white);color:var(--navy)}
.btn-sky{background:var(--accent);color:var(--white)}
.btn-light{background:var(--white);color:var(--ink)}

/* hero */
.hero{top:0;left:0;width:1200px;height:685px;background:linear-gradient(100deg,#9a9a9a 0%,#b9b9b9 35%,#c9c9c9 60%,#a8a8a8 100%)}
.hero-shade{top:0;left:0;width:1200px;height:685px;background:linear-gradient(90deg,rgba(40,40,40,.45) 0%,rgba(40,40,40,.15) 55%,rgba(40,40,40,.05) 100%)}
.brand{display:flex;align-items:center;gap:8px;font-family:"Poppins",sans-serif;font-weight:600}
.brand-mark{width:16px;height:16px;background:var(--accent);border-radius:3px}
.nav{top:43px;left:459px;display:flex;gap:33px;font-family:"Poppins",sans-serif;font-size:16px;color:var(--white)}
.nav .active{font-weight:600;border-bottom:2px solid var(--white);padding-bottom:2px}
.hero h1{top:258px;left:94px;font-size:48px;line-height:60px;color:var(--white)}
.hero p{top:386px;left:96px;width:470px;font-size:16px;line-height:31px;color:var(--white)}

/* about */
.about h2{top:770px;left:98px;font-size:33px;color:var(--ink)}
.about-copy{top:826px;left:99px;width:460px;font-size:15.5px;line-height:31px;color:var(--text)}
.about-copy p+p{margin-top:31px}
.about-visual{top:790px;left:676px;width:396px;height:410px;border-radius:48px;background:linear-gradient(135deg,#e3e3e3,#9c9c9c 45%,#6f8fa6 70%,#cfd8df)}

/* practice */
.practice{top:1286px;left:0;width:1200px;height:748px;background:linear-gradient(120deg,var(--navy-dark) 0%,var(--navy) 45%,#0a4477 60%,var(--navy) 100%)}
.practice h2{top:67px;left:99px;font-size:33px;color:var(--white)}
.rule{position:absolute;left:99px;height:1px;background:var(--line)}
.row-icon{position:absolute;left:99px;width:56px;height:56px}
.row-title{position:absolute;left:178px;font-family:"Poppins",sans-serif;font-weight:600;font-size:22px;color:var(--white)}
.row-text{position:absolute;left:430px;width:580px;font-size:15.5px;line-height:31px;color:var(--white)}

/* quote */
.quote{top:2034px;left:0;width:1200px;height:457px;background:linear-gradient(90deg,#cfe3e6 0%,#b7d6db 40%,#9fc6cc 70%,#c7dde0 100%)}
.quote-floor{left:0;top:384px;width:1200px;height:73px;background:linear-gradient(180deg,#e9eef0,#d6dfe2)}
.quote-photo{top:10px;left:790px;width:320px;height:440px;border-radius:40% 40% 20% 20%;background:radial-gradient(ellipse at 50% 40%,#f4f8f9,#c8dadf 70%,rgba(200,218,223,0))}
.quote h2{top:84px;left:97px;font-size:33px;line-height:48px;color:var(--ink)}
.quote p{top:182px;left:98px;width:460px;font-size:15.5px;line-height:31px;color:var(--text)}

/* contact */
.contact{top:2491px;left:0;width:1200px;height:615px;background:linear-gradient(120deg,#1a1a1b 0%,var(--charcoal) 50%,#272728 70%,var(--charcoal) 100%)}
.contact h2{top:74px;left:99px;font-size:33px;color:var(--white)}
.contact .lead{top:128px;left:99px;width:940px;font-size:15.5px;line-height:31px;color:var(--white)}
.field{position:absolute;border:1px solid #cfcfcf;color:var(--white);font-size:15.5px;padding:12px 0 0 25px}

/* footer */
.footer{top:3106px;left:0;width:1200px;height:296px;background:var(--white)}
.footer-nav{top:84px;left:417px;display:flex;gap:42px;font-family:"Poppins",sans-serif;font-size:15.5px;color:var(--ink)}
.contact-item{position:absolute;top:146px;display:flex;align-items:center;gap:16px;font-family:"Poppins",sans-serif;font-size:15.5px;color:var(--ink)}
.contact-dot{width:33px;height:33px;border-radius:50%;background:var(--accent);display:flex;align-items:center;justify-content:center}
.copyright{top:210px;left:417px;font-family:"Poppins",sans-serif;font-size:15px;color:var(--ink)}
.copyright i .hl{color:var(--accent)}
.code{top:216px;left:1117px;font-family:"Poppins",sans-serif;font-size:11px;color:var(--ink)}
</style>
</head>
<body>

<section class="abs hero" role="img" aria-label="Photograph of a dentist treating a patient in a bright dental surgery">
  <div class="abs hero-shade"></div>
</section>
<div class="abs brand" style="top:44px;left:99px;color:var(--white);font-size:17px"><span class="brand-mark"></span>Assure Dental Supply</div>
<nav class="abs nav">
  <span class="active">Home</span><span>About</span><span>Why Halden &amp; Crest</span><span>Areas of Practice</span><span>FAQs</span><span>Contact Us</span>
</nav>
<div class="hero">
  <h1 class="abs display">Welcome To<br>Assure <span class="hl">Dental</span> Supply</h1>
  <p class="abs">Lorem ipsum dolor sit amet, consectetur adipiscing elit, sed do eiusmod tempor incididunt ut labore et dolore magna aliqua.</p>
</div>
<a class="btn btn-blue" style="top:467px;left:96px;width:132px;height:46px">Get Started</a>

<section class="about">
  <h2 class="abs display">About Assure <span class="hl">Dental</span> Supply</h2>
  <div class="abs about-copy">
    <p>Sed ut perspiciatis unde omnis iste natus error sit voluptatem accusantium doloremque laudantium, totam rem aperiam, eaque vitae dicta sunt explicabo. Nemo enim ipsam voluptatem quia voluptas sit aspernatur aut odit aut fugit, nesciunt.</p>
    <p>Neque porro quisquam est, qui dolorem ipsum quia dolor sit amet, consectetur, adipisci velit, incidunt ut labore et dolore magnam aliquam quaerat voluptatem. Ut enim ad minima veniam, quis nostrum exercitationem ullam aliquid ex ea commodi consequatur?</p>
  </div>
  <div class="abs about-visual" role="img" aria-label="Framed photograph of a smiling dental patient"></div>
  <a class="btn btn-blue" style="top:1151px;left:99px;width:132px;height:48px">Read More</a>
</section>

<section class="abs practice">
  <h2 class="abs display">Areas of Practice</h2>
  <div class="rule" style="top:146px;width:900px"></div>

  <svg class="row-icon" style="top:196px" viewBox="0 0 56 56" fill="none" stroke="#fff" stroke-width="2">
    <rect x="4" y="22" width="20" height="16"/><rect x="28" y="10" width="22" height="16"/><path d="M32 10v16M38 10v16M44 10v16"/><circle cx="10" cy="42" r="3"/><circle cx="20" cy="42" r="3"/><path d="M30 44h20M4 50h48" stroke-dasharray="3 3"/>
  </svg>
  <div class="row-title" style="top:209px">Distribution</div>
  <div class="row-text" style="top:172px">Lorem ipsum dolor sit amet, consectetur adipiscing elit, sed do eiusmod tempor incididunt ut labore et dolore magna aliqua. Ut enim ad minim veniam, quis nostrud exercitation ullamco laboris nisi ut aliquip ex ea commodo consequat.</div>
  <div class="rule" style="top:294px;width:874px"></div>

  <svg class="row-icon" style="top:334px" viewBox="0 0 56 56" fill="none" stroke="#fff" stroke-width="2">
    <rect x="4" y="14" width="48" height="40"/><rect x="20" y="3" width="16" height="11"/><path d="M28 5v7M24.5 8.5h7"/><rect x="10" y="24" width="14" height="14"/><rect x="32" y="28" width="12" height="26"/><path d="M4 20h48"/>
  </svg>
  <div class="row-title" style="top:347px">Pharma</div>
  <div class="row-text" style="top:327px">Lorem ipsum dolor sit amet, consectetur adipiscing elit, sed do eiusmod tempor incididunt ut labore et dolore magna aliqua.</div>
  <div class="rule" style="top:433px;width:874px"></div>

  <svg class="row-icon" style="top:478px" viewBox="0 0 56 56" fill="none" stroke="#fff" stroke-width="2">
    <circle cx="30" cy="22" r="14"/><circle cx="30" cy="22" r="7"/><path d="M30 4v4M30 36v4M12 22h4M44 22h4M6 34v18h18M46 40v12" /><rect x="8" y="38" width="14" height="10"/>
  </svg>
  <div class="row-title" style="top:493px">Capital Equipment</div>
  <div class="row-text" style="top:459px">Lorem ipsum dolor sit amet, consectetur adipiscing elit, sed do eiusmod tempor incididunt ut labore et dolore magna aliqua. Ut enim ad minim veniam, quis nostrud exercitation ullamco laboris nisi ut aliquip ex ea commodo consequat.</div>
  <div class="rule" style="top:580px;width:874px"></div>

  <a class="btn btn-white" style="top:621px;left:99px;width:132px;height:48px">View More</a>
</section>

<section class="abs quote">
  <div class="abs quote-floor"></div>
  <div class="abs quote-photo" role="img" aria-label="Photograph of a white tooth model with a dental mirror"></div>
  <h2 class="abs display">“Where Transparency Starts”<br>Assure <span class="hl">Dental</span> Supply</h2>
  <p class="abs">Lorem ipsum dolor sit amet, consectetur adipiscing elit, sed do eiusmod tempor incididunt ut labore et dolore magna aliqua. Ut enim ad minim veniam, quis nostrud exercitation ullamco laboris nisi ut aliquip ex ea commodo consequat.</p>
  <a class="btn btn-sky" style="top:327px;left:98px;width:132px;height:48px">View More</a>
</section>

<section class="abs contact">
  <h2 class="abs display">Get in Touch</h2>
  <p class="abs lead">Lorem ipsum dolor sit amet, consectetur adipiscing elit, sed do eiusmod tempor incididunt ut labore et dolore magna aliqua. Ut enim ad minim veniam, quis nostrud exercitation ullamco laboris nisi ut aliquip ex ea commodo consequat.</p>
  <div class="field" style="top:223px;left:98px;width:456px;height:46px">Name</div>
  <div class="field" style="top:223px;left:577px;width:456px;height:46px">Email</div>
  <div class="field" style="top:298px;left:98px;width:456px;height:46px">Phone</div>
  <div class="field" style="top:298px;left:577px;width:456px;height:46px">Address</div>
  <div class="field" style="top:369px;left:98px;width:935px;height:89px">Message</div>
  <a class="btn btn-light" style="top:488px;left:98px;width:133px;height:47px">Contact Us</a>
</section>

<footer class="abs footer">
  <div class="abs brand" style="top:192px;left:98px;color:var(--ink);font-size:18px"><span class="brand-mark"></span>Assure Dental Supply</div>
  <nav class="abs footer-nav"><span>Home</span><span>About</span><span>Why Halden &amp; Crest</span><span>Areas of Practice</span><span>FAQs</span><span>Contact Us</span></nav>
  <div class="contact-item" style="left:413px">
    <span class="contact-dot"><svg width="16" height="16" viewBox="0 0 24 24" fill="#fff"><path d="M6.6 10.8a15.1 15.1 0 0 0 6.6 6.6l2.2-2.2a1 1 0 0 1 1-.25 11.4 11.4 0 0 0 3.6.57 1 1 0 0 1 1 1V20a1 1 0 0 1-1 1A17 17 0 0 1 3 4a1 1 0 0 1 1-1h3.5a1 1 0 0 1 1 1c0 1.25.2 2.45.57 3.57a1 1 0 0 1-.25 1z"/></svg></span>
    +1 800 555 0142
  </div>
  <div class="contact-item" style="left:654px">
    <span class="contact-dot"><svg width="16" height="16" viewBox="0 0 24 24" fill="none" stroke="#fff" stroke-width="2"><path d="M2 5h20v14H2z"/><path d="M2 6l10 7 10-7"/></svg></span>
    info@assuredentalsupply.com
  </div>
  <div class="abs copyright">Copyrights@2023. <i>Assure <span class="hl">Dental</span> Supply.</i> All Rights Reserved</div>
  <div class="abs code">C56</div>
</footer>

</body>
</html>
```